IT Services Company Needs Corporate PPT Template

This is urgent (need a fast turn around). We need a corporate PPT template deck (NOTE: Deck should be in 4:3 ratio) for our IT Services firm that is clean but slick and modern. We tend to lean more towards the flat design look. I'm attaching a zip file which includes our Corporate Branding Guide (which is in progress), color scheme, A PPT deck as inspiration (our logo is on the last slide), our font (LATO). Our newly launched website is located at: http://www.veranthix.com.

As an example of a deck we like see: http://slidemorrow.net/item/clean-multipurpose-business-presentation-template/5318206?WT.ac=category_thumb&WT.seg_1=category_thumb&WT.z_author=PixelHarbor
Although we don't want "this" deck - it gives an idea of style.

I'm also attaching a copy of our corporate deck as it is now to give you an idea of the type of content that would appear on various slides. We definitely want the following slides (at least) within the template:

Title Slide
Blank Slide
2 Column - with bullets
2 Column - no bullets
Single Column - no bullets
Single Column - with bullets
Various Charts and Tables (see example deck)
Meet the Team
Offering Slide
Customer Showcase
Timeline
Case Study
Contact US

Note: Being awarded this job will lead to a second job of creating our corporate deck.

Target Market(s)

CIO, CEO, Technology Officers, Sales People, Marketing, IT heads and staff, Customers, Prospective customers

Industry/Entity Type

Business

Requirements
Must have
• See description and attached files

```html
<!DOCTYPE html>
<html lang="en">
<head>
<meta charset="utf-8">
<title>Timeline Slide</title>
<link href="https://fonts.googleapis.com/css2?family=Lato:wght@400;700;900&display=swap" rel="stylesheet">
<style>
  :root {
    --header-dark: #0a5479;
    --header-mid: #0e6791;
    --header-title: #a6d6ee;
    --footer: #0a7aa8;
    --footer-dark: #086a93;
    --hex-fill: #3a99e2;
    --hex-edge: #0b5a80;
    --item-title: #1785b5;
    --body-text: #555a5e;
    --white: #ffffff;
  }
  * { margin: 0; padding: 0; box-sizing: border-box; }
  html, body { width: 1200px; height: 900px; overflow: hidden; }
  body { font-family: "Lato", sans-serif; background: var(--white); }

  .slide {
    position: relative;
    width: 1200px;
    height: 900px;
    background: linear-gradient(to bottom, #f1f2f3 0%, #ffffff 12%, #ffffff 85%, #eeeff0 100%);
    overflow: hidden;
  }

  .slide-header {
    position: absolute; left: 0; top: 0;
    width: 1200px; height: 87px;
    background: linear-gradient(to right, var(--header-dark), var(--header-mid) 60%, var(--header-dark));
  }
  .slide-header .pointer {
    position: absolute; left: 52px; top: 87px;
    width: 0; height: 0;
    border-left: 23px solid transparent;
    border-right: 23px solid transparent;
    border-top: 21px solid var(--header-dark);
  }
  .slide-title {
    position: absolute; left: 27px; top: 18px;
    font-size: 40px; font-weight: 700;
    color: var(--header-title);
    letter-spacing: 0.2px;
  }

  .milestone { position: absolute; left: 0; width: 1200px; height: 120px; }
  .milestone .hex { position: absolute; left: 508px; top: 0; width: 150px; height: 120px; }
  .milestone .year {
    position: absolute; left: 510px; top: 0;
    width: 138px; height: 120px;
    display: flex; align-items: center; justify-content: center;
    font-size: 38px; font-weight: 700; color: var(--white);
  }
  .milestone .detail { position: absolute; top: 9px; width: 420px; }
  .milestone.right .detail { left: 680px; text-align: left; }
  .milestone.left .detail { left: 63px; text-align: right; }
  .detail-title {
    font-size: 21px; font-weight: 700;
    color: var(--item-title);
    line-height: 28px;
  }
  .detail-text {
    font-size: 16px; color: var(--body-text);
    line-height: 27px;
  }

  .slide-footer {
    position: absolute; left: 0; top: 840px;
    width: 1200px; height: 60px;
    background: linear-gradient(to right, var(--footer-dark), var(--footer));
  }
  .brand-name {
    position: absolute; left: 20px; top: 12px;
    font-size: 30px; font-weight: 900; color: var(--white);
    letter-spacing: 0.5px;
  }
  .connect-label {
    position: absolute; left: 819px; top: 20px;
    font-size: 15px; font-weight: 700; color: var(--white);
  }
  .social-list {
    position: absolute; left: 975px; top: 13px;
    display: flex; align-items: center;
  }
  .social-slot {
    width: 30px; height: 30px;
    background: rgba(255,255,255,0.85);
    border-radius: 3px;
  }
  .social-divider {
    width: 2px; height: 34px;
    background: rgba(255,255,255,0.8);
    margin: 0 6px;
  }
</style>
</head>
<body>
<div class="slide">
  <header class="slide-header">
    <h1 class="slide-title">Project Title Here</h1>
    <span class="pointer"></span>
  </header>

  <section class="timeline">
    <div class="milestone right" style="top:111px">
      <svg class="hex" viewBox="0 0 150 120"><polygon points="9,60 41,0 115,0 147,60 115,120 41,120" fill="var(--hex-edge)"/><polygon points="2,60 34,0 108,0 140,60 108,120 34,120" fill="var(--hex-fill)"/></svg>
      <div class="year">1978</div>
      <div class="detail"><p class="detail-title">Title text here</p><p class="detail-text">consectetur adipiscing elit. Cras ipsum leo, vestibu-<br>lum non orci id, vehicula convallis sem.</p></div>
    </div>

    <div class="milestone left" style="top:256px">
      <svg class="hex" viewBox="0 0 150 120"><polygon points="-4,60 28,0 102,0 134,60 102,120 28,120" fill="var(--hex-edge)"/><polygon points="3,60 35,0 109,0 141,60 109,120 35,120" fill="var(--hex-fill)"/></svg>
      <div class="year">1989</div>
      <div class="detail" style="top:16px"><p class="detail-title">Title text here</p><p class="detail-text">consectetur adipiscing elit. Cras ipsum leo, vestibu-<br>lum non orci id, vehicula convallis sem.</p></div>
    </div>

    <div class="milestone right" style="top:401px">
      <svg class="hex" viewBox="0 0 150 120"><polygon points="9,60 41,0 115,0 147,60 115,120 41,120" fill="var(--hex-edge)"/><polygon points="2,60 34,0 108,0 140,60 108,120 34,120" fill="var(--hex-fill)"/></svg>
      <div class="year">1997</div>
      <div class="detail" style="top:16px"><p class="detail-title">Title text here</p><p class="detail-text">consectetur adipiscing elit. Cras ipsum leo, vestibu-<br>lum non orci id, vehicula convallis sem.</p></div>
    </div>

    <div class="milestone left" style="top:545px">
      <svg class="hex" viewBox="0 0 150 120"><polygon points="-4,60 28,0 102,0 134,60 102,120 28,120" fill="var(--hex-edge)"/><polygon points="3,60 35,0 109,0 141,60 109,120 35,120" fill="var(--hex-fill)"/></svg>
      <div class="year">2008</div>
      <div class="detail" style="top:13px"><p class="detail-title">Title text here</p><p class="detail-text">consectetur adipiscing elit. Cras ipsum leo, vestibu-<br>lum non orci id, vehicula convallis sem.</p></div>
    </div>

    <div class="milestone right" style="top:690px">
      <svg class="hex" viewBox="0 0 150 120"><polygon points="9,60 41,0 115,0 147,60 115,120 41,120" fill="var(--hex-edge)"/><polygon points="2,60 34,0 108,0 140,60 108,120 34,120" fill="var(--hex-fill)"/></svg>
      <div class="year">2013</div>
      <div class="detail" style="top:18px"><p class="detail-title">Title text here</p><p class="detail-text">consectetur adipiscing elit. Cras ipsum leo, vestibu-<br>lum non orci id, vehicula convallis sem.</p></div>
    </div>
  </section>

  <footer class="slide-footer">
    <span class="brand-name">Veranthix</span>
    <span class="connect-label">CONNECT WITH US:</span>
    <div class="social-list" aria-label="Social channels">
      <span class="social-slot"></span><span class="social-divider"></span>
      <span class="social-slot"></span><span class="social-divider"></span>
      <span class="social-slot"></span><span class="social-divider"></span>
      <span class="social-slot"></span><span class="social-divider"></span>
      <span class="social-slot"></span>
    </div>
  </footer>
</div>
</body>
</html>
```